Puffy Clouds Cotton Candy

Looking for a logo design and business cards to help a 13 year old entrepreneur promote her cotton candy business.
Contact Information for Business Card
Name, Phone & Email
Colors
E54698
E96AAD
F1A4CE
F9D9EA
FCEFF6
A7469A
B969AE
D3A5CF
EDDBEB
F8F0F9
6B429C
8869AF
B7A5CE
E3DAEB
F3F0F8
Requirements
Must have
- A fun feel that is appropriate for a teenage girl selling cotton candy

```html
<!DOCTYPE html>
<html lang="en">
<head>
<meta charset="utf-8">
<title>Puffy Clouds Cotton Candy – Business Cards</title>
<link rel="stylesheet" href="https://fonts.googleapis.com/css2?family=Fredoka:wght@500;600&display=swap">
<style>
  :root {
    --backdrop: #ab9a89;
    --card-white: #ffffff;
    --brand-purple: #6b429c;
    --brand-pink: #e54698;
    --pink-light: #f1a4ce;
    --shadow: rgba(40, 30, 20, 0.35);
  }
  * { margin: 0; padding: 0; box-sizing: border-box; }
  html, body {
    width: 1200px; height: 1200px; overflow: hidden;
    background: var(--backdrop);
    font-family: "Fredoka", sans-serif;
  }
  .canvas { position: relative; width: 1200px; height: 1200px; }
  .card {
    position: absolute; top: 480px;
    width: 420px; height: 240px; border-radius: 19px;
    box-shadow: 8px 8px 12px var(--shadow);
    overflow: hidden;
  }
  .card--front { left: 155px; background: var(--card-white); }
  .card--back { left: 624px; background: var(--brand-purple); }

  .wordmark {
    position: absolute; left: 0; right: 0;
    text-align: center; font-weight: 600; line-height: 1;
  }
  .wordmark__name { display: block; }
  .wordmark__tag { display: block; }
  .card--front .wordmark { top: 40px; color: var(--brand-pink); }
  .card--front .wordmark__name { font-size: 34px; }
  .card--front .wordmark__tag { font-size: 17px; margin-top: 8px; }
  .card--back .wordmark { top: 82px; color: var(--card-white); }
  .card--back .wordmark__name { font-size: 46px; }
  .card--back .wordmark__tag { font-size: 22px; margin-top: 10px; }

  .holder-name {
    position: absolute; top: 140px; left: 0; right: 0;
    text-align: center; font-size: 23px; font-weight: 600;
    color: var(--brand-pink);
  }
  .contact-rule {
    position: absolute; top: 180px; height: 1.5px; background: var(--brand-pink);
  }
  .contact-rule--left { left: 20px; width: 154px; }
  .contact-rule--right { left: 246px; width: 154px; }
  .contact-icons { position: absolute; top: 172px; left: 186px; width: 48px; height: 18px; }
  .contact-details {
    position: absolute; top: 196px; left: 0; right: 0;
    text-align: center; font-size: 12.5px; font-weight: 500;
    color: var(--brand-purple); line-height: 15px;
  }
</style>
</head>
<body>
<main class="canvas">
  <section class="card card--front" aria-label="Business card front">
    <div class="wordmark">
      <span class="wordmark__name">Puffy Clouds</span>
      <span class="wordmark__tag">Cotton Candy</span>
    </div>
    <h1 class="holder-name">Maya Brooks</h1>
    <div class="contact-rule contact-rule--left"></div>
    <svg class="contact-icons" viewBox="0 0 48 18" aria-hidden="true">
      <path d="M3 3 L6 1.5 L8.5 5.5 L6.5 7 Q8 11 11.5 12.5 L13 10.5 L17 13 L15.5 16 Q7 16 3 3 Z" fill="#6b429c"/>
      <rect x="30" y="4" width="16" height="11" rx="1" fill="#6b429c"/>
      <path d="M30.5 4.5 L38 10.5 L45.5 4.5" stroke="#fff" stroke-width="1.2" fill="none"/>
    </svg>
    <div class="contact-rule contact-rule--right"></div>
    <div class="contact-details">
      <p class="contact-phone">07. 5550. 1234</p>
      <p class="contact-email">maya@puffyclouds.com</p>
    </div>
  </section>

  <section class="card card--back" aria-label="Business card back">
    <div class="wordmark">
      <span class="wordmark__name">Puffy Clouds</span>
      <span class="wordmark__tag">Cotton Candy</span>
    </div>
  </section>
</main>
</body>
</html>
```